Brimlow OrthoLink IT Inc. new website

i need a website for my company which is dedicated to installation and service of computer systems in Dental Offices. I would like for it to encompass a technology feel and professional look. The company deals with all aspects of technology like, Audio Visual, computer systems and networks, Cloud services like data backup, data center. We provide manage services, support and services to Dental Professionals.
Updates

Looking for a Technology font but professional look Added Wednesday, April 20, 2016

Target Market(s)

Dental, Dentist

Industry/Entity Type

Dental

Number of Pages Required

5+ page

Font styles to use
Other font styles liked:
• Futuristic or Techy

Colors
0255a3
ec1f27

Requirements
Must have
• Tabs
Nice to have
• Have no idea maybe some suggestion on your part may help
Should not have
• A professional feel but have a techy look

```html
<!DOCTYPE html>
<html lang="en">
<head>
<meta charset="utf-8">
<title>Brimlow OrthoLink IT Inc.</title>
<link rel="stylesheet" href="https://fonts.googleapis.com/css2?family=Open+Sans:wght@400;600;700&family=Roboto+Condensed:wght@400;700&display=swap">
<style>
:root{
  --blue:#0255a3;
  --blue-dark:#014a8f;
  --ink:#111111;
  --text:#333333;
  --muted:#7a7a7a;
  --rule:#d6d6d6;
  --grey-band:#e6e6e6;
  --cta-grey:#e4e4e4;
  --footer:#2b2b2b;
  --footer-text:#bdbdbd;
  --white:#ffffff;
}
*{margin:0;padding:0;box-sizing:border-box}
html,body{width:1200px;height:2830px;overflow:hidden}
body{position:relative;background:var(--white);font-family:"Open Sans",Arial,sans-serif;color:var(--text)}
.abs{position:absolute}

/* top bar */
.topbar{left:0;top:0;width:1200px;height:42px;background:var(--ink);color:var(--white)}
.topbar .social{left:76px;top:13px;display:flex;gap:20px}
.topbar .social span{width:16px;height:16px;border-radius:50%;background:var(--white);display:block}
.topbar .contact{right:70px;top:0;height:42px;display:flex;align-items:center;gap:24px;font-size:19px}
.topbar .contact div{display:flex;align-items:center;gap:8px}
.topbar .contact .phone{font-weight:700;font-size:21px}

/* header */
.brand{left:79px;top:66px;display:flex;align-items:center;gap:12px}
.brand .mark{width:34px;height:34px;background:var(--blue);border-radius:4px}
.brand .name{font-family:"Roboto Condensed",sans-serif;font-weight:700;font-size:30px;color:var(--blue);line-height:1.1}
.nav{left:449px;top:77px;display:flex;height:44px;align-items:center}
.nav a{font-family:"Roboto Condensed",sans-serif;font-size:18px;color:#444;text-decoration:none;padding:0 15px;height:44px;line-height:44px}
.nav a.active{background:var(--blue);color:var(--white);border-radius:3px;padding:0 25px}

/* hero */
.hero{left:0;top:160px;width:1200px;height:491px}
.hero .photo{position:absolute;inset:0;background:linear-gradient(90deg,#f7fafd 0%,#e9f0f7 35%,#c9d7e6 60%,#aebfd2 80%,#d8e2ec 100%)}
.hero h1{left:78px;top:92px;font-family:"Open Sans",sans-serif;font-weight:700;font-size:44px;line-height:64px;color:var(--ink);letter-spacing:-1px}
.hero p{left:78px;top:222px;font-size:19px;line-height:30px;color:#222;width:430px}
.btn-primary{left:77px;top:304px;width:202px;height:59px;background:var(--blue);color:var(--white);border-radius:4px;font-family:"Roboto Condensed",sans-serif;font-weight:700;font-size:25px;display:flex;align-items:center;justify-content:center}

/* welcome */
.welcome-title{left:0;top:700px;width:1200px;text-align:center;font-size:38px;color:var(--ink);font-weight:400}
.welcome-title span{color:var(--blue)}
.welcome-text{left:180px;top:770px;width:840px;text-align:center;font-size:14.5px;line-height:24px;color:var(--muted)}
.btn-outline{left:455px;top:866px;width:313px;height:51px;border:2px solid #9bb3cc;border-radius:4px;background:#eef3f8;color:var(--blue);font-family:"Roboto Condensed",sans-serif;font-size:23px;display:flex;align-items:center;justify-content:center}
.hub-brand{left:0;top:990px;width:1200px;display:flex;justify-content:center;align-items:center;gap:12px}
.hub-brand .mark{width:34px;height:34px;background:var(--blue);border-radius:4px}
.hub-brand .name{font-family:"Roboto Condensed",sans-serif;font-weight:700;font-size:30px;color:var(--blue)}
.tree{left:0;top:1040px}
.service{width:360px;text-align:center}
.service .ring{width:125px;height:125px;border-radius:50%;border:2px solid #e2e2e2;margin:0 auto;display:flex;align-items:center;justify-content:center;background:var(--white)}
.service h3{font-family:"Roboto Condensed",sans-serif;font-weight:400;font-size:26px;color:var(--blue);margin-top:20px}
.service p{font-size:14.5px;line-height:25px;color:var(--muted);margin-top:10px;padding:0 50px}

/* technology */
.tech{left:0;top:1479px;width:1200px;height:468px;background:var(--grey-band)}
.section-title{width:1200px;text-align:center;font-family:"Roboto Condensed",sans-serif;font-size:40px;color:var(--ink);font-weight:400}
.section-title span{color:var(--blue)}
.tech-card{top:116px;width:313px;text-align:center}
.tech-card .media{width:313px;height:167px;border:1px solid #cfcfcf}
.tech-card h3{font-family:"Roboto Condensed",sans-serif;font-weight:400;font-size:23px;color:var(--blue);margin-top:22px}
.tech-card p{font-size:14.5px;line-height:25px;color:var(--muted);margin-top:8px;padding:0 4px}

/* testimonial */
.quote-mark{left:0;top:2060px;width:1200px;text-align:center;font-family:Georgia,serif;font-weight:700;font-size:90px;line-height:60px;color:#8a8a8a;height:50px}
.quote-text{left:215px;top:2126px;width:770px;text-align:center;font-size:14.5px;line-height:25px;color:var(--muted)}
.client-name{left:0;top:2226px;width:1200px;text-align:center;font-size:14.5px;font-weight:700;color:var(--blue)}
.arrow{top:2132px;width:64px;height:64px;border-radius:50%;border:2px solid var(--blue);display:flex;align-items:center;justify-content:center}

/* call to action */
.cta{left:77px;top:2298px;width:1046px;height:144px;background:var(--cta-grey);border:1px solid #d0d0d0;overflow:hidden}
.cta svg.band{position:absolute;left:0;top:0}
.cta .kicker{left:28px;top:24px;font-family:"Roboto Condensed",sans-serif;font-size:25px;color:var(--white);white-space:nowrap}
.cta .headline{left:26px;top:66px;font-family:"Roboto Condensed",sans-serif;font-size:34px;color:var(--white);white-space:nowrap}
.cta .call{left:604px;top:0;height:144px;display:flex;align-items:center;gap:18px;font-family:"Roboto Condensed",sans-serif;white-space:nowrap}
.cta .call .label{font-size:29px;color:var(--ink)}
.cta .call .ring{width:64px;height:64px;border-radius:50%;border:2px solid var(--ink);display:flex;align-items:center;justify-content:center}
.cta .call .num{font-weight:700;font-size:31px;color:var(--blue)}

/* footer */
.footer{left:0;top:2504px;width:1200px;height:326px;background:var(--footer);color:var(--footer-text)}
.footer h4{font-weight:400;font-size:19px;color:var(--white);margin-bottom:12px}
.footer .col{top:26px}
.links li{list-style:none;font-size:15px;line-height:31px;display:flex;align-items:center;gap:8px;color:#9a9a9a}
.links li.current{color:var(--white)}
.news p{font-size:14.5px;line-height:23px;color:var(--footer-text)}
.news .date{color:var(--white);margin-bottom:20px}
.newsletter p{font-size:14px;line-height:19px;color:var(--white);margin-bottom:12px}
.newsletter .field{width:234px;height:36px;border:1px solid #cfcfcf;color:var(--white);font-size:15px;padding:0 9px;line-height:34px;margin-bottom:10px}
.newsletter .btn{width:158px;height:41px;background:var(--blue);color:var(--white);font-size:20px;display:flex;align-items:center;justify-content:center;margin-top:4px}
.info .row{display:flex;gap:10px;font-size:15px;line-height:23px;color:var(--footer-text);margin-bottom:10px}
.info .phone{font-weight:700;font-size:21px;color:var(--white)}
.info .social{display:flex;gap:18px;margin-top:6px}
.info .social span{width:44px;height:44px;border-radius:50%;border:2px solid var(--white);display:block}
.info .social span.filled{background:var(--white)}
.footer .rule{left:77px;top:274px;width:1046px;height:1px;background:#444}
.footer .copy{left:0;top:290px;width:1200px;text-align:center;font-size:15px;color:var(--white)}
</style>
</head>
<body>

<!-- top bar -->
<div class="abs topbar">
  <div class="abs social"><span></span><span></span><span></span></div>
  <div class="abs contact">
    <div>
      <svg width="20" height="15" viewBox="0 0 20 15"><rect x="1" y="1" width="18" height="13" rx="1" fill="none" stroke="#fff" stroke-width="2"/><path d="M1 2l9 7 9-7" fill="none" stroke="#fff" stroke-width="2"/></svg>
      info@brimlowortholink.com
    </div>
    <div class="phone">
      <svg width="18" height="18" viewBox="0 0 24 24"><path fill="#fff" d="M6.6 10.8a15.1 15.1 0 006.6 6.6l2.2-2.2c.3-.3.7-.4 1-.2 1.1.4 2.3.6 3.6.6.6 0 1 .4 1 1V20c0 .6-.4 1-1 1A17 17 0 013 4c0-.6.4-1 1-1h3.5c.6 0 1 .4 1 1 0 1.3.2 2.5.6 3.6.1.3 0 .7-.2 1z"/></svg>
      555 014 7890
    </div>
  </div>
</div>

<!-- header -->
<div class="abs brand"><span class="mark"></span><span class="name">Brimlow OrthoLink IT</span></div>
<nav class="abs nav">
  <a class="active">HOME</a><a>ABOUT</a><a>SERVICES</a><a>SUPPORT</a><a>CLIENT</a><a>BLOG</a><a>CONTACT</a>
</nav>

<!-- hero -->
<section class="abs hero">
  <div class="photo" role="img" aria-label="Bright dental treatment room with instrument tray, cabinet and a wall monitor showing a panoramic dental x-ray"></div>
  <h1 class="abs">TECHNOLOGY FOR<br>BEST PRACTICE</h1>
  <p class="abs">f you view technology as an expense rather than an investment, you haven't worked with us.</p>
  <div class="abs btn-primary">CONTACT US</div>
</section>

<!-- welcome -->
<h2 class="abs welcome-title">Welcome to <span>Brimlow OrthoLink IT</span></h2>
<p class="abs welcome-text">Lorem Ipsum is simply dummy text of the printing and typesetting industry. Lorem Ipsum has been the industry's standard dummy text ever since the 1500s, when an unknown printer took a galley of type and scrambled it to make a type specimen book.</p>
<div class="abs btn-outline">GET OUR CUSTOM SUPPORT</div>

<div class="abs hub-brand"><span class="mark"></span><span class="name">Brimlow OrthoLink IT</span></div>
<svg class="abs tree" width="1200" height="160" viewBox="0 0 1200 160">
  <path d="M600 7V87M287 87H913M287 87V158M913 87V158" fill="none" stroke="#d8d8d8" stroke-width="2"/>
</svg>

<div class="abs service" style="left:107px;top:1197px">
  <div class="ring">
    <svg width="64" height="58" viewBox="0 0 64 58" fill="var(--blue)">
      <rect x="24" y="0" width="16" height="14" rx="2"/>
      <path d="M31 14v10M8 24h48M8 24v10M32 24v10M56 24v10" stroke="var(--blue)" stroke-width="3" fill="none"/>
      <rect x="0" y="36" width="16" height="14" rx="2"/><rect x="24" y="36" width="16" height="14" rx="2"/><rect x="48" y="36" width="16" height="14" rx="2"/>
    </svg>
  </div>
  <h3>Manage services</h3>
  <p>Lorem Ipsum is simply dummy text of the printing and typesetting.</p>
</div>

<div class="abs service" style="left:733px;top:1197px">
  <div class="ring">
    <svg width="64" height="58" viewBox="0 0 64 58">
      <circle cx="24" cy="32" r="13" fill="none" stroke="var(--blue)" stroke-width="7" stroke-dasharray="5 3.2"/>
      <circle cx="24" cy="32" r="8" fill="none" stroke="var(--blue)" stroke-width="5"/>
      <circle cx="48" cy="14" r="8" fill="none" stroke="var(--blue)" stroke-width="5" stroke-dasharray="4 2.3"/>
      <circle cx="50" cy="44" r="7" fill="none" stroke="var(--blue)" stroke-width="5" stroke-dasharray="4 2.3"/>
    </svg>
  </div>
  <h3>Support</h3>
  <p>Lorem Ipsum is simply dummy text of the printing and typesetting.</p>
</div>

<!-- technology -->
<section class="abs tech">
  <h2 class="abs section-title" style="left:0;top:50px">OUR <span>TECHNOLOGY</span></h2>
  <div class="abs tech-card" style="left:77px">
    <div class="media" role="img" aria-label="Doctor on the phone while working at a laptop" style="background:linear-gradient(135deg,#f4f7fa,#c9d3dd 55%,#eef2f5)"></div>
    <h3>Audio Visual</h3>
    <p>Lorem Ipsum is simply dummy text of the printing and typesetting industry. Lorem Ipsum has been the industry.</p>
  </div>
  <div class="abs tech-card" style="left:443px">
    <div class="media" role="img" aria-label="Computers, phones and servers linked to a central network cloud" style="background:radial-gradient(circle at 50% 50%,#cfe3f7,#f7f9fb 70%)"></div>
    <h3>Computer Systems and Networks</h3>
    <p>Lorem Ipsum is simply dummy text of the printing and typesetting industry. Lorem Ipsum has been the industry.</p>
  </div>
  <div class="abs tech-card" style="left:810px">
    <div class="media" role="img" aria-label="Cloud connected to laptop, desktop, tower and phone for data backup" style="background:linear-gradient(180deg,#e9ecef,#c7ccd2)"></div>
    <h3>Cloud Services of Data Backup</h3>
    <p>Lorem Ipsum is simply dummy text of the printing and typesetting industry. Lorem Ipsum has been the industry.</p>
  </div>
</section>

<!-- testimonial -->
<h2 class="abs section-title" style="left:0;top:1992px">WHAT OUR <span>CLIENT SAY</span></h2>
<div class="abs quote-mark">&ldquo;</div>
<p class="abs quote-text">Lorem Ipsum is simply dummy text of the printing and typesetting industry. Lorem Ipsum has been the industry's standard dummy text ever since the 1500.Lorem Ipsum is simply dummy text of the printing and typesetting industry.</p>
<div class="abs client-name">- Client Name</div>
<div class="abs arrow" style="left:77px"><svg width="20" height="32" viewBox="0 0 20 32"><path d="M16 2L3 16l13 14" fill="none" stroke="var(--ink)" stroke-width="2.5"/></svg></div>
<div class="abs arrow" style="left:1057px"><svg width="20" height="32" viewBox="0 0 20 32"><path d="M4 2l13 14L4 30" fill="none" stroke="var(--ink)" stroke-width="2.5"/></svg></div>

<!-- call to action -->
<section class="abs cta">
  <svg class="band" width="580" height="144" viewBox="0 0 580 144"><path d="M0 0H540L563 72 540 144H0Z" fill="var(--blue)"/></svg>
  <div class="abs kicker">WHAT ARE YOU WAITING FOR?</div>
  <div class="abs headline">BRIMLOW ORTHOLINK IT SUPPORT</div>
  <div class="abs call">
    <span class="label">CALL US ON</span>
    <span class="ring"><svg width="30" height="30" viewBox="0 0 24 24"><path fill="var(--ink)" d="M6.6 10.8a15.1 15.1 0 006.6 6.6l2.2-2.2c.3-.3.7-.4 1-.2 1.1.4 2.3.6 3.6.6.6 0 1 .4 1 1V20c0 .6-.4 1-1 1A17 17 0 013 4c0-.6.4-1 1-1h3.5c.6 0 1 .4 1 1 0 1.3.2 2.5.6 3.6.1.3 0 .7-.2 1z"/></svg></span>
    <span class="num">555 014 7890</span>
  </div>
</section>

<!-- footer -->
<footer class="abs footer">
  <div class="abs col" style="left:79px">
    <h4>Useful Links</h4>
    <ul class="links">
      <li class="current"><svg width="14" height="12" viewBox="0 0 14 12"><path d="M1 1l5 5-5 5M7 1l5 5-5 5" fill="none" stroke="currentColor" stroke-width="2"/></svg>Home</li>
      <li><svg width="14" height="12" viewBox="0 0 14 12"><path d="M1 1l5 5-5 5M7 1l5 5-5 5" fill="none" stroke="currentColor" stroke-width="2"/></svg>About</li>
      <li><svg width="14" height="12" viewBox="0 0 14 12"><path d="M1 1l5 5-5 5M7 1l5 5-5 5" fill="none" stroke="currentColor" stroke-width="2"/></svg>Services</li>
      <li><svg width="14" height="12" viewBox="0 0 14 12"><path d="M1 1l5 5-5 5M7 1l5 5-5 5" fill="none" stroke="currentColor" stroke-width="2"/></svg>Support</li>
      <li><svg width="14" height="12" viewBox="0 0 14 12"><path d="M1 1l5 5-5 5M7 1l5 5-5 5" fill="none" stroke="currentColor" stroke-width="2"/></svg>News</li>
      <li><svg width="14" height="12" viewBox="0 0 14 12"><path d="M1 1l5 5-5 5M7 1l5 5-5 5" fill="none" stroke="currentColor" stroke-width="2"/></svg>Contact</li>
    </ul>
  </div>
  <div class="abs col news" style="left:351px;width:240px">
    <h4>Latest News</h4>
    <p>Lorem Ipsum is simply dummy text of the printing.</p>
    <p class="date">21 April 2016</p>
    <p>Lorem Ipsum is simply dummy text of the printing.</p>
    <p class="date">21 April 2016</p>
  </div>
  <div class="abs col newsletter" style="left:621px;width:250px">
    <h4>Newsletter</h4>
    <p>Subscribe to stay on Brimlow OrthoLink IT.</p>
    <div class="field">Enter Name</div>
    <div class="field">Enter Email</div>
    <div class="btn">SUBSCRIBE</div>
  </div>
  <div class="abs col info" style="left:893px;width:240px">
    <h4>Contact Info</h4>
    <div class="row"><svg width="14" height="20" viewBox="0 0 14 20" style="flex:none;margin-top:2px"><path d="M7 0a7 7 0 017 7c0 5-7 13-7 13S0 12 0 7a7 7 0 017-7z" fill="#fff"/><circle cx="7" cy="7" r="2.5" fill="var(--footer)"/></svg><span>Lorem Ipsum is simply dummy text of the printing.</span></div>
    <div class="row phone"><svg width="18" height="18" viewBox="0 0 24 24" style="margin-top:3px"><path fill="#fff" d="M6.6 10.8a15.1 15.1 0 006.6 6.6l2.2-2.2c.3-.3.7-.4 1-.2 1.1.4 2.3.6 3.6.6.6 0 1 .4 1 1V20c0 .6-.4 1-1 1A17 17 0 013 4c0-.6.4-1 1-1h3.5c.6 0 1 .4 1 1 0 1.3.2 2.5.6 3.6.1.3 0 .7-.2 1z"/></svg>555 014 7890</div>
    <div class="row"><svg width="18" height="14" viewBox="0 0 20 15" style="margin-top:5px"><rect x="1" y="1" width="18" height="13" rx="1" fill="none" stroke="#fff" stroke-width="2"/><path d="M1 2l9 7 9-7" fill="none" stroke="#fff" stroke-width="2"/></svg>info@brimlowortholink.com</div>
    <div class="social"><span class="filled"></span><span></span><span></span></div>
  </div>
  <div class="abs rule"></div>
  <div class="abs copy">&copy; BRIMLOW ORTHOLINK IT - 2016. All Rights Reserved.</div>
</footer>

</body>
</html>
```